Eye Catching Email Marketing design

Our health care consulting firm is based in New York City. We sell health care consulting Services to medical practices (doctors). We need a powerful email marketing design to use as one of our primary selling tools to attract new clients. The Design should convey health care knowledge, expertise professionalism, cutting edge technology and the services we offer. <br/>The design should incorporate our logo and its colors (blue and white) but we want it to be eye catching and vibrant, so other colors be included. We are open to the designer's creativity. Any pictures used should show diversity (races)and should include women. Designers can find our logo and other graphics on our website at www harbor ridge advisory.com. Please feel free to ask questions.<br/><br/>

Target Market(s)

Health care professionals, executives and Doctors.

Colors

Designer to choose colors to be used in the design.

Requirements
Nice to have
• What ever the design feels will help make this design vibrant

```html
<!DOCTYPE html>
<html lang="en">
<head>
<meta charset="utf-8">
<title>Harbor Ridge Advisory — Email</title>
<link rel="stylesheet" href="https://fonts.googleapis.com/css2?family=Montserrat:wght@400;500;600;700&family=Source+Sans+3:wght@300;400;600&family=Ubuntu:wght@500;700&display=swap">
<style>
  :root{
    --blue:#0f56a3;
    --frame:#0d55a4;
    --green:#8dc021;
    --green-tile:#8fc320;
    --cyan:#29a6dc;
    --ink:#1b1b1b;
    --text:#3a3a3a;
    --muted:#777;
    --white:#ffffff;
  }
  *{margin:0;padding:0;box-sizing:border-box}
  html,body{width:1200px;height:4926px;overflow:hidden;background:var(--white)}
  body{position:relative;font-family:"Source Sans 3",sans-serif;color:var(--text)}
  .abs{position:absolute}

  .hero-band{left:0;top:0;width:1200px;height:1147px;
    background:
      radial-gradient(ellipse 260px 520px at 40px 700px,rgba(214,180,170,.55),transparent 70%),
      radial-gradient(ellipse 280px 560px at 1160px 450px,rgba(90,185,230,.55),transparent 70%),
      linear-gradient(100deg,#c9d9e6 0%,#eef3f8 22%,#ffffff 50%,#e9f3fa 75%,#b9dbef 100%)}
  .brand{left:0;top:30px;width:1200px;text-align:center;font-family:"Montserrat",sans-serif;
    font-weight:700;color:var(--blue);font-size:62px;letter-spacing:2px}
  .brand-sub{left:0;top:146px;width:1200px;text-align:center;font-family:"Montserrat",sans-serif;
    font-weight:600;color:var(--blue);font-size:25px;letter-spacing:2px}
  .hero-photo{left:151px;top:199px;width:898px;height:595px;
    background:
      radial-gradient(ellipse 200px 230px at 450px 250px,rgba(222,176,150,.9),transparent 75%),
      radial-gradient(ellipse 170px 200px at 250px 330px,rgba(120,80,60,.8),transparent 75%),
      radial-gradient(ellipse 170px 200px at 670px 330px,rgba(110,75,55,.8),transparent 75%),
      radial-gradient(ellipse 170px 220px at 800px 300px,rgba(225,190,160,.8),transparent 75%),
      linear-gradient(180deg,#5e7a3e 0%,#849a5c 30%,#a89a80 58%,#6f7a4a 80%,#505a34 100%)}

  .services-frame{left:147px;top:793px;width:906px;height:694px;background:var(--frame)}
  .tile{width:422px;height:316px;background:var(--green-tile);color:var(--white)}
  .tile h3{position:absolute;top:48px;font-family:"Ubuntu",sans-serif;font-weight:700;font-size:38px;line-height:47px}
  .tile a{position:absolute;top:228px;font-size:24px;color:var(--white);text-decoration:underline}
  .tile.left h3,.tile.left a{left:16px}
  .tile.right h3,.tile.right a{right:26px;text-align:right}
  .tl{left:172px;top:818px}
  .tr{left:608px;top:818px}
  .bl{left:172px;top:1148px}
  .br{left:608px;top:1148px}
  .bl h3,.br h3{top:42px}
  .bl a,.br a{top:222px}
  .hub{left:428px;top:969px;width:344px;height:344px}

  .section-title{left:0;width:1200px;text-align:center;font-family:"Montserrat",sans-serif;font-size:60px;line-height:68px;color:var(--ink);font-weight:400}
  .section-title strong{display:block;color:var(--blue);font-weight:600}
  .rule{left:573px;width:54px;height:6px;background:var(--cyan)}
  .copy{font-size:26px;line-height:48px;color:var(--text);font-weight:300}
  .button{width:226px;height:71px;background:var(--green);color:var(--white);font-family:"Montserrat",sans-serif;
    font-weight:600;font-size:23px;display:flex;align-items:center;justify-content:center;left:487px}

  .welcome-copy{left:159px;top:1801px;width:883px;text-align:justify;text-align-last:center}

  .expertise-photo{left:0;top:2335px;width:1200px;height:1258px;
    background:
      radial-gradient(ellipse 260px 340px at 430px 640px,rgba(60,45,40,.85),transparent 75%),
      radial-gradient(ellipse 250px 330px at 930px 640px,rgba(235,230,225,.9),transparent 75%),
      radial-gradient(ellipse 240px 120px at 560px 1150px,rgba(245,245,245,.85),transparent 75%),
      linear-gradient(180deg,#ffffff 0%,#ffffff 28%,#dfe7ec 42%,#aebfc7 58%,#8d8f8a 72%,#8a6a50 86%,#6b4f3a 100%)}
  .expertise-copy{left:150px;top:2535px;width:900px;text-align:center;font-size:25px}

  .contact-label{left:0;width:1200px;text-align:center;font-size:25px;color:var(--muted)}
  .contact-value{left:0;width:1200px;text-align:center;font-family:"Montserrat",sans-serif;font-weight:600;font-size:27px;color:var(--ink)}
  .team{left:0;top:3842px;width:1200px;text-align:center;font-family:"Montserrat",sans-serif;font-weight:600;font-size:38px;color:var(--blue)}
  .icon-disc{left:542px;width:116px;height:116px;border-radius:50%;background:var(--green);display:flex;align-items:center;justify-content:center}

  .footer{left:0;top:4632px;width:1200px;height:294px;background:linear-gradient(90deg,#0a4a92,#0e5bab 50%,#0a4a92)}
  .social{top:4686px;width:80px;height:80px;border-radius:50%;border:2px solid var(--white);
    display:flex;align-items:center;justify-content:center;color:var(--white);font-size:17px;font-weight:600}
  .footer-links{left:0;top:4796px;width:1200px;text-align:center;font-size:20px;color:var(--white)}
  .footer-links span{margin:0 9px}
  .copyright{left:0;top:4848px;width:1200px;text-align:center;font-size:19px;color:var(--white)}
</style>
</head>
<body>

<div class="abs hero-band"></div>
<div class="abs brand">HARBOR RIDGE</div>
<div class="abs brand-sub">HARBOR RIDGE ADVISORY LLC</div>
<div class="abs hero-photo" role="img" aria-label="Photo of a smiling woman with four children of diverse backgrounds outdoors among greenery"></div>

<div class="abs services-frame"></div>
<div class="abs tile left tl"><h3>Revenue Cycle<br>Management</h3><a>View Details</a></div>
<div class="abs tile right tr"><h3>Compliance<br>Management</h3><a>View Details</a></div>
<div class="abs tile left bl"><h3>Practice<br>Management</h3><a>View Details</a></div>
<div class="abs tile right br"><h3>Healthcare<br>Innovation</h3><a>View Details</a></div>

<svg class="abs hub" viewBox="0 0 344 344" aria-hidden="true">
  <circle cx="172" cy="172" r="172" fill="#fff"/>
  <rect x="164" y="0" width="16" height="344" fill="var(--frame)"/>
  <rect x="0" y="164" width="344" height="16" fill="var(--frame)"/>
  <g fill="none" stroke="var(--blue)" stroke-width="8" stroke-linecap="round">
    <path d="M68 86 A32 32 0 0 1 122 70"/>
    <path d="M132 102 A32 32 0 0 1 78 118"/>
  </g>
  <path d="M114 58 L130 74 L110 80 Z" fill="var(--blue)"/>
  <path d="M86 130 L70 114 L90 108 Z" fill="var(--blue)"/>
  <g transform="translate(218,60)">
    <rect x="6" y="4" width="48" height="62" rx="4" fill="none" stroke="var(--blue)" stroke-width="7"/>
    <path d="M30 22 l14 5 v10 c0 9-6 14-14 17 c-8-3-14-8-14-17 v-10z" fill="var(--blue)"/>
    <path d="M24 37 l5 5 l9-10" fill="none" stroke="#fff" stroke-width="4"/>
  </g>
  <g transform="translate(62,212)">
    <circle cx="40" cy="22" r="14" fill="none" stroke="var(--blue)" stroke-width="7"/>
    <path d="M8 40 c0 14 8 22 18 26 l0 14 M72 40 c0 14-8 22-18 26 l0 14" fill="none" stroke="var(--blue)" stroke-width="8" stroke-linecap="round"/>
  </g>
  <g transform="translate(214,212)">
    <circle cx="38" cy="36" r="30" fill="none" stroke="var(--blue)" stroke-width="8" stroke-dasharray="10 6"/>
    <circle cx="38" cy="28" r="10" fill="var(--blue)"/>
    <path d="M20 56 c2-12 10-16 18-16 s16 4 18 16z" fill="var(--blue)"/>
  </g>
</svg>

<div class="abs section-title" style="top:1608px">Welcome To<strong>Harbor Ridge Advisory</strong></div>
<div class="abs rule" style="top:1763px"></div>
<p class="abs copy welcome-copy">Harbor Ridge Advisory (HRA), founded in 2015, is a Management Services Organization &amp; Healthcare Consulting Firm skilled at helping medical practices advance their strategic vision in an ever-evolving healthcare system. Harbor Ridge Advisory specializes in Revenue Cycle Management, Practice Management, Compliance Management &amp; Healthcare Innovation.</p>
<div class="abs button" style="top:2083px">Read More</div>

<div class="abs expertise-photo" role="img" aria-label="Photo of two colleagues, a man and a woman, reviewing charts at a laptop in a bright office"></div>
<div class="abs section-title" style="top:2335px">Expertise Your Medical<strong>Practice Deserves</strong></div>
<div class="abs rule" style="top:2502px"></div>
<p class="abs copy expertise-copy">The expertise of our team encompasses full spectrum knowledge in revenue<br>cycle management, practice management, regulatory compliance,<br>and healthcare innovation.</p>
<div class="abs button" style="top:2723px">Read More</div>

<div class="abs section-title" style="top:3715px">Still Have Questions?</div>
<div class="abs rule" style="top:3809px"></div>
<div class="abs team">Talk to a Member of Our Team</div>

<div class="abs icon-disc" style="top:3923px">
  <svg width="40" height="40" viewBox="0 0 24 24" aria-hidden="true"><path fill="#fff" d="M6.6 10.8a15.2 15.2 0 0 0 6.6 6.6l2.2-2.2c.3-.3.7-.4 1-.2 1.1.4 2.3.6 3.6.6.6 0 1 .4 1 1V20c0 .6-.4 1-1 1A17 17 0 0 1 3 4c0-.6.4-1 1-1h3.5c.6 0 1 .4 1 1 0 1.3.2 2.5.6 3.6.1.3 0 .7-.2 1z"/></svg>
</div>
<div class="abs contact-label" style="top:4052px">Phone :</div>
<div class="abs contact-value" style="top:4092px">(646) 555-0142</div>

<div class="abs icon-disc" style="top:4173px">
  <svg width="40" height="40" viewBox="0 0 24 24" aria-hidden="true"><path fill="#fff" d="M2 5h20v2l-10 6L2 7z M2 9l10 6 10-6v10H2z"/></svg>
</div>
<div class="abs contact-label" style="top:4301px">Email :</div>
<div class="abs contact-value" style="top:4342px">info@harborridgeadvisory.com</div>
<div class="abs button" style="top:4430px">Subscribe</div>

<div class="abs footer"></div>
<div class="abs social" style="left:468px">Like</div>
<div class="abs social" style="left:560px">Post</div>
<div class="abs social" style="left:652px">Join</div>
<div class="abs footer-links">Terms of service<span>|</span>Privacy statement<span>|</span>User agreement<span>|</span>Careers<span>|</span>Contact Us</div>
<div class="abs copyright">Copyrights © 2020 All Rights Reserved</div>

</body>
</html>
```